Harborline Renewal Business Card Design

Professional and clean design. The design colors should flow with the logo. Two-sided card with the website on the back which is:

www.HarborlineRenewal.example.

"Specializing in Water Damage Restoration"

On the front I need the name, email, phone, and logo.

Name: Darnell Quisby
Email: Darnell@HarborlineRenewal.example
Phone: 555-318-2046 for now

I only have the Preview and Thumbnail right now but should have the source files uploaded within a day or two.

Target Market(s)

Flood victims, home owners with water damage from busted pipes etc...

Industry/Entity Type

Business

Contact Information for Business Card

Name: Darnell Quisby

Font styles to use
Serif
Sans Serif

Requirements
Must have
• Business Card Details Info

```html
<!DOCTYPE html>
<html lang="en">
<head>
<meta charset="utf-8">
<title>Harborline Renewal Business Card</title>
<link href="https://fonts.googleapis.com/css2?family=Cinzel:wght@400;600&family=Open+Sans:wght@400&display=swap" rel="stylesheet">
<style>
  :root {
    --backdrop: #e8e3da;
    --ink-black: #060606;
    --brand-blue: #2e95d3;
    --brand-sky: #5ac0ec;
    --paper-white: #ffffff;
    --serif: 'Cinzel', 'Trajan Pro', serif;
    --sans: 'Open Sans', Arial, sans-serif;
  }
  * { margin: 0; padding: 0; box-sizing: border-box; }
  html, body { width: 1200px; height: 1121px; overflow: hidden; background: var(--backdrop); }
  .canvas { position: relative; width: 1200px; height: 1121px; }

  .card {
    position: absolute;
    width: 841px;
    height: 480px;
    border-radius: 18px;
    overflow: hidden;
    background: var(--ink-black);
  }
  .card-front { left: 48px; top: 55px; }
  .card-back { left: 308px; top: 590px; }

  .card-shapes { position: absolute; inset: 0; width: 100%; height: 100%; }

  .brand-mark {
    position: absolute;
    border-radius: 50%;
    background: var(--brand-blue);
  }
  .card-front .brand-mark { left: 200px; top: 30px; width: 74px; height: 74px; }
  .card-back .brand-mark { left: 368px; top: 48px; width: 104px; height: 104px; }

  .brand-name {
    position: absolute;
    left: 0;
    text-align: center;
    font-family: var(--serif);
    font-weight: 600;
    color: var(--brand-blue);
    text-transform: uppercase;
    line-height: 1.15;
  }
  .card-front .brand-name { width: 474px; top: 126px; font-size: 40px; letter-spacing: 1px; }
  .card-back .brand-name { width: 841px; top: 196px; font-size: 54px; letter-spacing: 2px; }

  .holder { position: absolute; right: 24px; top: 30px; text-align: right; font-family: var(--serif); }
  .holder-name { color: var(--paper-white); font-size: 25px; font-weight: 600; letter-spacing: 0.5px; }
  .holder-title { color: var(--brand-blue); font-size: 20px; letter-spacing: 2px; margin-top: 2px; }

  .contact-list {
    position: absolute; right: 24px; top: 356px;
    list-style: none; text-align: right;
    font-family: var(--sans); font-size: 20px; color: var(--paper-white);
  }
  .contact-list li { height: 36px; display: flex; align-items: center; justify-content: flex-end; gap: 10px; }
  .contact-icon { width: 18px; height: 18px; }

  .address {
    position: absolute; left: 43px; top: 402px;
    font-family: var(--sans); font-size: 20px; color: var(--paper-white);
    font-style: normal; line-height: 34px;
  }

  .tagline {
    position: absolute; left: 0; width: 841px; top: 404px;
    text-align: center; font-family: var(--serif); font-size: 23px;
    color: var(--brand-sky); letter-spacing: 1px;
  }
</style>
</head>
<body>
<main class="canvas">

  <section class="card card-front" aria-label="Card front">
    <svg class="card-shapes" viewBox="0 0 641 366" preserveAspectRatio="none" aria-hidden="true">
      <rect width="641" height="366" fill="var(--ink-black)"/>
      <ellipse cx="150" cy="55" rx="262" ry="198" fill="var(--brand-blue)"/>
      <ellipse cx="150" cy="55" rx="252" ry="189" fill="var(--paper-white)" stroke="var(--ink-black)" stroke-width="2"/>
      <path d="M0,188 C120,300 360,280 641,196 L641,366 L0,366 Z" fill="var(--brand-blue)"/>
      <path d="M0,205 C130,305 370,288 641,210" fill="none" stroke="var(--ink-black)" stroke-width="7"/>
      <path d="M0,222 C140,312 380,295 641,222" fill="none" stroke="var(--ink-black)" stroke-width="3"/>
    </svg>

    <span class="brand-mark" aria-hidden="true"></span>
    <h1 class="brand-name">Harborline<br>Renewal</h1>

    <div class="holder">
      <p class="holder-name">Darnell Quisby</p>
      <p class="holder-title">Title</p>
    </div>

    <ul class="contact-list">
      <li>
        <svg class="contact-icon" viewBox="0 0 24 24" aria-hidden="true"><path fill="var(--paper-white)" d="M6.6 10.8a15 15 0 0 0 6.6 6.6l2.2-2.2c.3-.3.7-.4 1-.2 1.1.4 2.3.6 3.6.6.6 0 1 .4 1 1V20c0 .6-.4 1-1 1A17 17 0 0 1 3 4c0-.6.4-1 1-1h3.5c.6 0 1 .4 1 1 0 1.3.2 2.5.6 3.6.1.3 0 .7-.2 1z"/></svg>
        555-318-2046
      </li>
      <li>
        <svg class="contact-icon" viewBox="0 0 24 24" aria-hidden="true"><rect x="2" y="5" width="20" height="14" rx="2" fill="var(--paper-white)"/><path d="M3 6l9 7 9-7" fill="none" stroke="var(--brand-blue)" stroke-width="2"/></svg>
        Darnell@HarborlineRenewal.example
      </li>
      <li>
        <svg class="contact-icon" viewBox="0 0 24 24" aria-hidden="true"><g fill="none" stroke="var(--paper-white)" stroke-width="2"><circle cx="12" cy="12" r="9"/><ellipse cx="12" cy="12" rx="4" ry="9"/><path d="M3 12h18"/></g></svg>
        www.HarborlineRenewal.example
      </li>
    </ul>

    <address class="address">Street Name, City Name<br>Zipcode-12345</address>
  </section>

  <section class="card card-back" aria-label="Card back">
    <span class="brand-mark" aria-hidden="true"></span>
    <h2 class="brand-name">Harborline<br>Renewal</h2>
    <p class="tagline">Specializing in Water Damage Restoration</p>
  </section>

</main>
</body>
</html>
```